www.marvenholt.com

Updating website so looks futristic but yet business like and easy to navigate, essentially a good landing page with a cool picture summing up what we do, and links to the following pages, all other pages on site to be updated, Exclusive Distributor of Brisk Forge Unique Fitness Equipment Products in UK & Ireland, www.crestvolley.co.uk Exclusive Partners & Distributors Of Crest Volley - Obstacle Races - Obstacle Hire - Obstacle Training - Adventure Events, www.goplumwick.co.uk Adventures That Inspire. We also Health Club / Facillity Consultancy

```html
<!DOCTYPE html>
<html lang="en">
<head>
<meta charset="utf-8">
<title>Marvenholt Leisure – Health, Wellness, Fitness, Consultants</title>
<link href="https://fonts.googleapis.com/css2?family=Marcellus+SC&family=Marcellus&family=Libre+Baskerville&family=Lato:wght@400;700;900&family=Open+Sans:ital,wght@0,400;0,600;1,400&display=swap" rel="stylesheet">
<style>
:root{
  --yellow:#e8c300;
  --yellow-soft:#f0d21e;
  --ink:#1b1b1b;
  --black:#0c0c0c;
  --grey:#6d6d6d;
  --line:#d9d9d9;
  --white:#ffffff;
}
*{box-sizing:border-box;margin:0;padding:0}
html,body{width:1200px;height:4545px;overflow:hidden}
body{font-family:"Open Sans",Arial,sans-serif;color:var(--ink);background:var(--white);position:relative}
section,header,footer{position:absolute;left:0;width:1200px;overflow:hidden}
.abs{position:absolute}
.media{position:absolute}
.heading{font-family:"Marcellus SC",serif;font-weight:400;text-align:center;color:var(--ink)}
.heading em{font-style:normal;color:var(--yellow)}
.sub{font-family:"Open Sans",sans-serif;font-style:italic;font-size:15px;text-align:center}
.btn{position:absolute;display:flex;align-items:center;justify-content:center;background:var(--yellow);color:var(--white);font-family:"Lato",sans-serif;font-weight:700;font-size:17px;border-radius:30px;letter-spacing:.5px}
.field{position:absolute;background:var(--white);font-size:13px;color:#777;padding:0 16px;display:flex;align-items:center}

/* hero */
.hero{top:0;height:680px}
.hero .media{inset:0;background:linear-gradient(180deg,#d6dfe6 0%,#a9b4bc 30%,#6f7478 60%,#3d3a36 100%)}
.hero .shade{position:absolute;inset:0;background:linear-gradient(180deg,rgba(255,255,255,.15) 0%,rgba(0,0,0,0) 40%,rgba(0,0,0,.55) 100%)}
.brand{position:absolute;left:91px;top:22px;color:var(--ink)}
.brand-name{font-family:"Marcellus",serif;font-size:42px;line-height:1;white-space:nowrap}
.brand-tag{font-family:"Libre Baskerville",serif;font-size:16px;margin-top:6px;white-space:nowrap}
.top-cta{left:957px;top:10px;width:164px;height:45px;font-size:17px}
.nav{position:absolute;top:62px;left:474px;display:flex;gap:4px;font-family:"Lato",sans-serif;font-size:14px;color:var(--white)}
.nav span{padding:11px 15px;border-radius:22px}
.nav .active{background:var(--yellow)}
.hero-title{position:absolute;left:76px;top:488px;font-family:"Lato",sans-serif;font-weight:900;font-size:70px;color:var(--yellow)}
.hero-sub{position:absolute;left:76px;top:585px;font-family:"Libre Baskerville",serif;font-size:29px;color:var(--white)}

/* welcome */
.welcome{top:680px;height:456px;background:var(--white)}
.welcome .media{left:600px;top:90px;width:600px;height:340px;background:radial-gradient(ellipse at 55% 55%,#c9d6e4 0%,#eef1f4 70%,#ffffff 100%)}
.welcome-card{position:absolute;left:76px;top:60px;width:627px;height:375px;background:var(--white);border:1px solid var(--line);box-shadow:0 2px 14px rgba(0,0,0,.18)}
.welcome-card .heading{margin-top:52px;font-size:36px}
.welcome-card p{width:520px;margin:22px auto 0;text-align:center;font-size:14px;line-height:26px;color:#444}
.welcome-card .btn{left:220px;top:278px;width:186px;height:56px}

/* consultation */
.consult{top:1136px;height:364px;background:linear-gradient(180deg,#2a2a2a,#1a1a1a)}
.consult .heading{color:var(--white);position:absolute;top:58px;width:100%;font-size:46px}
.consult .sub{position:absolute;top:118px;width:100%;color:#ddd;font-style:normal;font-size:16px}
.consult .field{top:165px;height:56px}
.consult .btn{left:509px;top:243px;width:185px;height:54px}

/* expertise */
.expert{top:1500px;height:797px;background:var(--white)}
.expert .heading{position:absolute;top:54px;width:100%;font-size:46px}
.expert .sub{position:absolute;top:112px;width:100%}
.tab{position:absolute;top:170px;width:212px;height:60px;border:2px solid #ecd86a;border-radius:30px;font-family:"Marcellus SC",serif;font-size:24px;color:var(--yellow);display:flex;align-items:center;justify-content:center}
.tab.active{background:var(--yellow);color:var(--white);border-color:var(--yellow)}
.expert .media{left:197px;top:273px;width:803px;height:318px;background:linear-gradient(90deg,#d9c8b8 0%,#8fc24a 30%,#f1f1f1 50%,#8fc24a 70%,#d5c2b0 100%)}
.expert p{position:absolute;left:150px;top:612px;width:900px;text-align:center;font-size:14px;line-height:26px;color:#555}
.expert .btn{left:507px;top:679px;width:186px;height:57px}

/* build business */
.build{top:2297px;height:418px;background:linear-gradient(90deg,#1f2b3a 0%,#3b4a5c 55%,#6d7f93 100%)}
.build .media{left:840px;top:0;width:360px;height:418px;background:linear-gradient(180deg,#8a9cb0 0%,#3d5477 60%,#1d2a44 100%)}
.build .heading{position:absolute;left:127px;top:66px;text-align:left;color:var(--white);font-size:46px}
.build .sub{position:absolute;left:300px;top:128px;color:#ddd;font-size:15px}
.build .btn{left:306px;top:297px;width:182px;height:54px}

/* events */
.events{top:2715px;height:503px;background:var(--white)}
.events .heading{position:absolute;top:52px;width:100%;font-size:46px}
.events .sub{position:absolute;top:116px;width:100%}
.event{position:absolute;top:179px;width:506px;height:264px}
.event .media{left:0;top:0;width:242px;height:264px}
.event .txt{position:absolute;left:266px;top:26px;width:236px}
.event h3{font-family:"Marcellus SC",serif;font-weight:400;font-size:20px}
.event .date{font-family:"Marcellus",serif;color:var(--yellow);font-size:17px;margin-top:14px}
.event p{font-size:13px;line-height:22px;color:#555;margin-top:14px}
.event .more{font-family:"Marcellus SC",serif;color:var(--yellow);font-size:16px;margin-top:16px}

/* testimonials */
.testimonials{top:3218px;height:452px;background:var(--yellow)}
.testimonials .media{inset:0;background:linear-gradient(90deg,rgba(255,255,255,.08),rgba(0,0,0,.06),rgba(255,255,255,.1))}
.testimonials .heading{position:absolute;top:58px;width:100%;font-size:46px}
.client-mark{left:566px;top:108px;width:68px;height:68px;border-radius:50%;background:#b3141b;border:3px solid var(--black)}
.client-name{position:absolute;top:194px;width:100%;text-align:center;font-size:14px;color:var(--ink)}
.client-name b{font-family:"Marcellus SC",serif;font-weight:400;font-size:19px}
.quote{position:absolute;left:152px;top:238px;width:893px;height:122px;border:1px solid rgba(255,255,255,.9);padding:18px 40px;font-style:italic;color:var(--white);font-size:14px;line-height:24px;text-align:center}
.arrow{position:absolute;top:278px;width:40px;height:42px;background:var(--white);display:flex;align-items:center;justify-content:center}
.dots{position:absolute;top:392px;left:556px;display:flex;gap:18px}
.dots i{width:14px;height:14px;border-radius:50%;background:var(--ink)}
.dots i.on{background:var(--white)}

/* videos */
.videos{top:3670px;height:405px;background:var(--white)}
.v-tile{position:absolute;width:288px;height:202px;background:var(--white);display:flex;flex-direction:column;align-items:center;justify-content:center;gap:18px}
.v-tile h4{font-family:"Marcellus SC",serif;font-weight:400;font-size:24px;white-space:nowrap}
.v-tile span{border:2px solid var(--yellow);color:var(--yellow);font-family:"Marcellus SC",serif;font-size:20px;padding:9px 30px;border-radius:30px}

/* footer */
.site-footer{top:4075px;height:470px;background:var(--black);color:#ccc}
.foot-cta{position:absolute;top:34px;left:0;width:100%;display:flex;justify-content:center;align-items:center;gap:30px;font-size:16px;color:var(--white)}
.foot-cta .btn{position:static;width:170px;height:48px}
.foot-rule{position:absolute;left:0;top:108px;width:100%;height:1px;background:#333}
.foot-brand{position:absolute;left:50px;top:180px;width:270px;text-align:center;color:var(--white)}
.foot-brand .brand-name{font-size:27px}
.foot-brand .brand-tag{font-size:12px;margin-top:6px}
.socials{position:absolute;left:140px;top:252px;display:flex;gap:16px}
.socials i{width:42px;height:42px;border-radius:50%;border:2px solid var(--yellow)}
.foot-col{position:absolute;top:136px}
.foot-col h5{font-family:"Lato",sans-serif;font-size:17px;color:var(--yellow);font-weight:700;letter-spacing:.5px;margin-bottom:16px}
.foot-col li{list-style:none;font-size:14px;line-height:32px;color:#ddd}
.foot-col li::before{content:"» ";color:#ddd}
.contact-row{display:flex;gap:14px;font-size:14px;line-height:22px;color:#ddd;margin-bottom:22px}
.contact-row svg{flex:none;margin-top:2px}
.news p{font-size:14px;line-height:22px;width:250px;color:#ddd}
.news .input{margin-top:22px;width:250px;height:42px;background:var(--white);display:flex;align-items:center;justify-content:space-between;padding-left:12px;font-size:13px;color:#777}
.news .input b{width:42px;height:42px;background:var(--yellow);display:flex;align-items:center;justify-content:center}
.news .btn{position:static;margin-top:16px;width:166px;height:44px;font-size:16px}
.copyright{position:absolute;top:422px;width:100%;text-align:center;font-size:14px;color:#ccc}
.copyright b{color:var(--yellow);font-weight:400}
</style>
</head>
<body>

<header class="hero">
  <div class="media" role="img" aria-label="Photo of a group training on rowing and resistance machines in a bright studio"></div>
  <div class="shade"></div>
  <div class="brand">
    <div class="brand-name">Marvenholt Leisure</div>
    <div class="brand-tag">Health, Wellness, Fitness, Consultants</div>
  </div>
  <div class="btn top-cta">BRISK FORGE</div>
  <nav class="nav">
    <span class="active">HOME</span><span>HEALTH</span><span>WELLNESS</span><span>FITNESS</span><span>OUR TEAM</span><span>TESTIMONIALS</span><span>CONTACT</span>
  </nav>
  <h1 class="hero-title">Ready To Start ?</h1>
  <div class="hero-sub">Health, Wellness, Fitness, Consultants</div>
</header>

<section class="welcome">
  <div class="media" role="img" aria-label="Photo of two smiling athletes in sportswear stretching on the floor"></div>
  <div class="welcome-card">
    <h2 class="heading">Welcome To <em>Marvenholt Leisure</em></h2>
    <p>Marvenholt Leisure are leading consultants to the Health, Wellness and Fitness industry, with over 25 years experience working with some of the biggest global worldwide brands from equipment providers and facility operators to mass participation events and obstacle course races.</p>
    <div class="btn">LEARN MORE</div>
  </div>
</section>

<section class="consult">
  <h2 class="heading">Need Free <em>Consultation</em></h2>
  <div class="sub">Need a free quote, or have a question? Get in touch!</div>
  <div class="field" style="left:133px;width:306px">Name *</div>
  <div class="field" style="left:448px;width:300px">Email *</div>
  <div class="field" style="left:760px;width:303px">Phone *</div>
  <div class="btn">SUBMIT</div>
</section>

<section class="expert">
  <h2 class="heading">We Are <em>Expert In</em></h2>
  <div class="sub">We Provide You Our Best Services</div>
  <div class="tab active" style="left:267px">Health</div>
  <div class="tab" style="left:494px">Wellness</div>
  <div class="tab" style="left:724px">Fitness</div>
  <div class="media" role="img" aria-label="Photo of a diverse group of people holding up green letter boards spelling health"></div>
  <p>Marvenholt Leisure are leading consultants to the Health, Wellness and Fitness industry, with over 25 years experience working with some of the biggest global worldwide brands from equipment providers and facility operators.</p>
  <div class="btn">LEARN MORE</div>
</section>

<section class="build">
  <div class="media" role="img" aria-label="Photo of a woman running in a blue sports top"></div>
  <h2 class="heading">Build Your <em>Business Today</em></h2>
  <div class="sub">Leave a Message</div>
  <div class="field" style="left:88px;top:172px;width:300px;height:50px">Name*</div>
  <div class="field" style="left:400px;top:172px;width:300px;height:50px">Subject*</div>
  <div class="field" style="left:88px;top:228px;width:300px;height:48px">Email*</div>
  <div class="field" style="left:400px;top:228px;width:300px;height:48px">Message*</div>
  <div class="btn">SUBMIT</div>
</section>

<section class="events">
  <h2 class="heading">Marvenholt Leisure <em>Event's</em></h2>
  <div class="sub">Recent Post</div>
  <article class="event" style="left:76px">
    <div class="media" role="img" aria-label="Photo of runners crossing a muddy obstacle course"
      style="background:linear-gradient(160deg,#b9c4b0 0%,#7f8a6a 50%,#5b4a3a 100%)"></div>
    <div class="txt">
      <h3>Marvenholt Leisure</h3>
      <div class="date">11 Oct 2017</div>
      <p>Lorem Ipsum is simply dummy text of the printing and typesetting industry. Lorem Ipsum has been.</p>
      <div class="more">Read More.. &#8250;</div>
    </div>
  </article>
  <article class="event" style="left:615px">
    <div class="media" role="img" aria-label="Photo of a fitness class exercising in a swimming pool"
      style="background:linear-gradient(170deg,#3a3e44 0%,#6b7c86 45%,#3fa6c8 100%)"></div>
    <div class="txt">
      <h3>Marvenholt Leisure</h3>
      <div class="date">11 Oct 2017</div>
      <p>Lorem Ipsum is simply dummy text of the printing and typesetting industry. Lorem Ipsum has been.</p>
      <div class="more">Read More.. &#8250;</div>
    </div>
  </article>
</section>

<section class="testimonials">
  <div class="media" role="img" aria-label="Faint photo of a gym floor behind a yellow overlay"></div>
  <h2 class="heading">What Our <em style="color:var(--ink)">Client Say</em></h2>
  <div class="abs client-mark"></div>
  <div class="client-name"><b>– Dale Ferrow</b> – Ridgeline Race CEO &amp; Founder of Ridgeline Race</div>
  <div class="arrow" style="left:122px"><svg width="12" height="16" viewBox="0 0 12 16"><path d="M10 1 3 8l7 7" fill="none" stroke="#333" stroke-width="2.5"/></svg></div>
  <div class="arrow" style="left:1038px"><svg width="12" height="16" viewBox="0 0 12 16"><path d="M2 1l7 7-7 7" fill="none" stroke="#333" stroke-width="2.5"/></svg></div>
  <div class="quote">" Stridewell Ridgeline Race and Marvenholt Leisure first collaborated in 2015. Neil and the Marvenholt team have showed respectable drive, commitment, passion and integrity throughout our partnership. With the help of the Marvenholt team Ridgeline Race have gained huge success in the UK in 2015 and we are ro..."</div>
  <div class="dots"><i></i><i class="on"></i><i></i></div>
</section>

<section class="videos">
  <div class="media" role="img" aria-label="Photo of women stretching on yoga mats in a studio"
    style="left:0;top:0;width:624px;height:405px;background:linear-gradient(110deg,#c9b7a6 0%,#9c8a7c 45%,#5e5a66 100%)"></div>
  <svg class="abs" style="left:232px;top:142px" width="122" height="122" viewBox="0 0 122 122">
    <circle cx="61" cy="61" r="57" fill="rgba(0,0,0,.25)" stroke="#fff" stroke-width="5"/>
    <path d="M48 36 88 61 48 86Z" fill="#fff"/>
  </svg>
  <div class="media" role="img" aria-label="Photo of a group workout class"
    style="left:624px;top:0;width:288px;height:202px;background:linear-gradient(160deg,#d9d4cf 0%,#8c8580 55%,#3e3a38 100%)"></div>
  <div class="v-tile" style="left:912px;top:0"><h4>Marvenholt Leisure</h4><span>Watch Now</span></div>
  <div class="v-tile" style="left:624px;top:202px;height:203px"><h4>Marvenholt Leisure</h4><span>Watch Now</span></div>
  <div class="media" role="img" aria-label="Photo of an indoor cycling class"
    style="left:912px;top:202px;width:288px;height:203px;background:linear-gradient(160deg,#e6e3df 0%,#9a9590 50%,#3a3634 100%)"></div>
</section>

<footer class="site-footer">
  <div class="foot-cta"><span>Our Unique Fitness Equipment Products in UK &amp; Ireland</span><div class="btn">BRISK FORGE</div></div>
  <div class="foot-rule"></div>
  <div class="foot-brand">
    <div class="brand-name">Marvenholt Leisure</div>
    <div class="brand-tag">Health, Wellness, Fitness, Consultants</div>
  </div>
  <div class="socials"><i></i><i></i></div>

  <div class="foot-col" style="left:342px">
    <h5>SITEMAP</h5>
    <ul><li style="color:var(--yellow)">Home</li><li>Health</li><li>Wellness</li><li>Fitness</li><li>Our Team</li><li>Testimonials</li><li>Contact Us</li></ul>
  </div>

  <div class="foot-col" style="left:606px;width:240px">
    <h5>CONTACT US</h5>
    <div class="contact-row"><svg width="16" height="20" viewBox="0 0 16 20"><path d="M8 1a6 6 0 0 0-6 6c0 5 6 12 6 12s6-7 6-12a6 6 0 0 0-6-6Z" fill="none" stroke="#ccc" stroke-width="1.6"/><circle cx="8" cy="7" r="2" fill="#ccc"/></svg><span>The Orchards, Cheshire UK &amp; Ireland</span></div>
    <div class="contact-row"><svg width="16" height="18" viewBox="0 0 16 18"><path d="M3 1h3l1.5 4-2 1.5a9 9 0 0 0 5 5L12 9.5l4 1.5v3a2 2 0 0 1-2 2A13 13 0 0 1 1 3a2 2 0 0 1 2-2Z" fill="none" stroke="#ccc" stroke-width="1.5"/></svg><span>07-555-210-480<br>01-555-408-912</span></div>
    <div class="contact-row"><svg width="18" height="14" viewBox="0 0 18 14"><rect x="1" y="1" width="16" height="12" fill="none" stroke="#ccc" stroke-width="1.5"/><path d="M1 1l8 7 8-7" fill="none" stroke="#ccc" stroke-width="1.5"/></svg><span>team@marvenholt.com</span></div>
    <div class="contact-row"><svg width="18" height="18" viewBox="0 0 18 18"><circle cx="9" cy="9" r="8" fill="none" stroke="#ccc" stroke-width="1.5"/><path d="M1 9h16M9 1c-4 4-4 12 0 16M9 1c4 4 4 12 0 16" fill="none" stroke="#ccc" stroke-width="1.3"/></svg><span>www.marvenholt.com</span></div>
  </div>

  <div class="foot-col news" style="left:873px">
    <h5>NEWSLETTER</h5>
    <p>Would you like to receive exclusive access to articles, white papers and our regular monthly newsletter?</p>
    <div class="input">Enter Email Id<b><svg width="18" height="14" viewBox="0 0 18 14"><rect x="1" y="1" width="16" height="12" fill="none" stroke="#fff" stroke-width="1.6"/><path d="M1 1l8 7 8-7" fill="none" stroke="#fff" stroke-width="1.6"/></svg></b></div>
    <div class="btn">SUBSCRIBE</div>
  </div>

  <div class="copyright">&copy;<b>Marvenholt Leisure</b> - 2017 All Right Reserved.</div>
</footer>

</body>
</html>
```